Creative, Modern Annual Report for Non-profit, Brightnest

We need a clean and creative annual report for a non-profit helping older kids find families. We are including a word document, some information is not complete, please see notes. The document has names of photos and thumbnails to help point you in the right direction. Please see dropbox file for everything you need. Thank you! https://www.filevaultex.com/sh/kq7trm2ux48bpl9/QWErt5YhnUIOPlk8JHgfdsAZxC?dl=0

Font styles to use
Sans Serif

Requirements
Must have
• Choose from these Branding Colors
• #Fex525
• #ff5000
• #00000
• #057688
• #5ab3c2

```html
<!DOCTYPE html>
<html lang="en">
<head>
<meta charset="utf-8">
<title>Weekend Bridges USA – Brightnest Annual Report</title>
<link href="https://fonts.googleapis.com/css2?family=Arimo:wght@400;700&display=swap" rel="stylesheet">
<style>
  :root {
    --gold: #fec525;
    --ink: #000000;
    --paper: #ffffff;
    --photo-dark: #1f3320;
    --photo-mid: #5a4a3c;
    --photo-light: #e9e2d6;
  }
  * { margin: 0; padding: 0; box-sizing: border-box; }
  html, body { width: 927px; height: 1200px; overflow: hidden; background: var(--paper); }
  .page {
    position: relative;
    width: 927px;
    height: 1200px;
    font-family: "Arimo", Arial, sans-serif;
    color: var(--ink);
  }
  .rule { position: absolute; left: 0; width: 927px; height: 40px; }
  .rule--top { top: 60px; }
  .rule--bottom { top: 1108px; }
  .brand-mark {
    position: absolute;
    left: 464px; top: 80px;
    transform: translate(-50%, -50%);
    font-size: 8px;
    font-weight: 700;
    color: var(--ink);
    letter-spacing: 0.2px;
  }
  .page-number {
    position: absolute;
    left: 464px; top: 1128px;
    transform: translate(-50%, -50%);
    font-size: 15px;
    color: var(--gold);
  }
  .title {
    position: absolute;
    top: 110px; left: 0; width: 927px;
    text-align: center;
    font-size: 29px;
    font-weight: 700;
  }
  .feature-photo {
    position: absolute;
    left: 95px; top: 189px;
    width: 725px; height: 448px;
    background: linear-gradient(90deg, var(--photo-dark) 0%, #2c3a26 38%, var(--photo-mid) 60%, var(--photo-light) 100%);
  }
  .story {
    position: absolute;
    left: 82px; top: 656px;
    width: 764px;
    font-size: 16.4px;
    line-height: 25.5px;
    text-align: justify;
  }
  .story p { text-indent: 27px; }
  .story p + p { margin-top: 25.5px; }
</style>
</head>
<body>
<div class="page">
  <svg class="rule rule--top" viewBox="0 0 927 40" aria-hidden="true">
    <line x1="54" y1="18.5" x2="873" y2="18.5" stroke="var(--gold)" stroke-width="1.4"/>
    <line x1="54" y1="22" x2="873" y2="22" stroke="var(--gold)" stroke-width="1.4"/>
    <circle cx="464" cy="20" r="25" fill="var(--paper)" stroke="var(--gold)" stroke-width="2"/>
  </svg>
  <span class="brand-mark">Brightnest</span>

  <h1 class="title">Weekend Bridges USA</h1>

  <div class="feature-photo" role="img" aria-label="Photo of a smiling teenage boy and an adult man bumping fists in front of a decorated holiday tree"></div>

  <div class="story">
    <p>Over 123,000 American children in foster care are waiting to be adopted. They are unable to return home. California and Texas have the most children in foster care. In California ____ children are in foster care and ___ are waiting for families. In Texas 16,958 are in foster care and more than 3,700 are still looking a family to call their own.</p>
    <p>Started in 2005, Weekend Bridges has found families and connections for 75% of the ___ children who have participated in the program. Kids who participate in Brightnest’s program have exhausted their chances to move back into their biological families. They live in large residential facilities, group homes, and foster families.</p>
    <p>Weekend Bridges recruits interested hosts and introduces them to the kids. The program lets the youth engage with adults that they like. Kids have choice in the adults who host them.</p>
  </div>

  <svg class="rule rule--bottom" viewBox="0 0 927 40" aria-hidden="true">
    <line x1="54" y1="18.5" x2="873" y2="18.5" stroke="var(--gold)" stroke-width="1.4"/>
    <line x1="54" y1="22" x2="873" y2="22" stroke="var(--gold)" stroke-width="1.4"/>
    <circle cx="464" cy="20" r="16" fill="var(--paper)" stroke="var(--gold)" stroke-width="1.6"/>
  </svg>
  <span class="page-number">5</span>
</div>
</body>
</html>
```